Etiketten-Design für Rotwein
Zielgruppe
Weinkellerei aus Baden (Deutschland) mit Fokus im Lebensmittelhandel in Deutschland
Aufgabenstellung
Wir suchen ein Frontetikett für einen modernen badischen Rotwein (Cuvée Lumen) mit dem Namen 'Die stille Seite vom Hang'
Aus dem Etikett soll hervorgehen, dass es sich nicht um einen klassischen, leichten deutschen Rotwein handelt, sondern um einen kräftigen, gehaltvollen, mediterran anmutenden Rotwein mit purpurroter Farbe und vollmundigem, nachhaltigem Geschmack. (Geschmacksrichtung feinherb)
Zielgruppe Discount-Kunden, Männlich/Weiblich, Alter: 25-60 Jahre, wird für unter € 5,-/Fl. verkauft.
Weinbeschreibung:
Farbe: Ein wunderschönes tiefdunkles purpurrot mit violetten Reflexen
Duft: In der Nase zeigen sich Aromen nach Waldbeeren, sowie Anklänge von Rauch, Röstaromen, Nelke, etwas Vanille und dunkle Schokolade
Geschmack: Geschmacklich füllig und kraftvoll, Brombeeraromen und schön eingebundenen Tanninen. Langanhaltend intensiv im Abgang.
Anforderungen Etikett:
Maße: Höhe max. 120mm/Breite max. 80mm (darf auch kleiner oder quadratisch sein)
SK Etikett, Naturstruktur bis 90g (m²) (Ein - oder zweiteilig)
Eine figürliche Etikettenkontur ist möglich, es wird aber am rechten Etikettenrand eine gerade Spendekante benötigt um das Etikett maschinell verarbeiten zu können.
Als Flasche wird eine 0,75 L Bordeauxflasche (Farbe: grün) eingesetzt.
Verschluss: Longcap
Mögliche Veredelungen: Quelllack, Prägungen, Heissfolie, Glanzlack
Pflichtangaben:
Die stille Seite vom Hang

```html
<!DOCTYPE html>
<html lang="de">
<head>
<meta charset="utf-8">
<title>Die stille Seite vom Hang – Frontetikett</title>
<link rel="stylesheet" href="https://fonts.googleapis.com/css2?family=Open+Sans:wght@400;800&display=swap">
<style>
  :root {
    --backdrop: #8a0016;
    --label-black: #1a1a1a;
    --title-ink: #1b1b1b;
    --title-glow: rgba(235, 200, 205, 0.45);
    --leaf-deep: #4a0c16;
    --leaf-mid: #5c1220;
    --cuvee-red: #8e1a24;
  }
  * { margin: 0; padding: 0; box-sizing: border-box; }
  html, body {
    width: 1200px;
    height: 840px;
    overflow: hidden;
    background: var(--backdrop);
  }
  .canvas {
    position: relative;
    width: 1200px;
    height: 840px;
    background: var(--backdrop);
  }
  .label {
    position: absolute;
    left: 340px;
    top: 30px;
    width: 520px;
    height: 780px;
    background: var(--label-black);
    overflow: hidden;
  }
  .leaf-illustration {
    position: absolute;
    left: 4px;
    top: 141px;
    width: 512px;
    height: 540px;
    border-radius: 46% 46% 40% 40%;
    background: radial-gradient(ellipse at 50% 58%, var(--leaf-mid) 0%, var(--leaf-deep) 45%, rgba(40, 10, 16, 0.6) 72%, rgba(26, 26, 26, 0) 100%);
  }
  .wine-name {
    position: absolute;
    left: 40px;
    top: 118px;
    font-family: "Open Sans", sans-serif;
    font-weight: 800;
    font-size: 84px;
    line-height: 152px;
    letter-spacing: -1px;
    color: var(--title-ink);
    text-transform: uppercase;
    text-shadow: 0 0 10px var(--title-glow), 0 0 4px var(--title-glow);
  }
  .wine-name span { display: block; white-space: nowrap; }
  .cuvee {
    position: absolute;
    left: 0;
    width: 100%;
    top: 738px;
    text-align: center;
    font-family: "Open Sans", sans-serif;
    font-weight: 400;
    font-size: 25px;
    color: var(--cuvee-red);
  }
</style>
</head>
<body>
<main class="canvas">
  <section class="label">
    <div class="leaf-illustration" role="img" aria-label="Illustration eines dunkelroten Weinblatts"></div>
    <h1 class="wine-name">
      <span>Die</span>
      <span>Stille</span>
      <span>Seite vom</span>
      <span>Hang</span>
    </h1>
    <p class="cuvee">Cuvée Lumen</p>
  </section>
</main>
</body>
</html>
```